Business card for law firm

Need business card for new law firm. Think confident, authoritative, conservative, but not stuffy or old-fashioned.

Contact Information for Business Card

Content for card - logo (uploaded), plus the following:

Paul Whitcombe (larger font)
Managing Partner (larger font, but not as large as name)
Level 9, 7 Ferris Lane
Sydney NSW 2000
Main Tel 02 9364 2710
Direct Tel 02 8472 3159
Email paul@qvlegal.com.au
www.qvlegal.com.au

Letterhead design should include logo plus:
Level 9, 7 Ferris Lane
Sydney NSW 2000
Tel 02 8472 3159
www.qvlegal.com.au

```html
<!DOCTYPE html>
<html lang="en">
<head>
<meta charset="utf-8">
<title>Quayview Legal – Business Card</title>
<link href="https://fonts.googleapis.com/css2?family=Cormorant+Garamond:wght@600;700&family=Nunito+Sans:wght@400;600&display=swap" rel="stylesheet">
<style>
  :root {
    --navy: #1c2467;
    --navy-deep: #141a52;
    --paper: #ffffff;
    --paper-shade: #eceef2;
    --backdrop: #d9dbe0;
    --silver: #e4e6ec;
  }
  * { box-sizing: border-box; margin: 0; padding: 0; }
  html, body {
    width: 1200px; height: 900px; overflow: hidden;
    background: var(--backdrop);
  }
  .sheet {
    width: 1200px; height: 900px;
    display: flex; flex-direction: column;
    align-items: center; justify-content: center; gap: 56px;
  }
  .card {
    width: 600px; height: 367px;
    position: relative;
    box-shadow: 0 6px 22px rgba(0,0,0,.18);
  }

  /* Front */
  .card--front {
    background: radial-gradient(ellipse at 70% 75%, var(--paper) 40%, var(--paper-shade) 100%);
    color: var(--navy);
  }
  .front-brand {
    position: absolute; left: 40px; top: 0; width: 210px; height: 100%;
    display: flex; flex-direction: column; align-items: center; justify-content: center; gap: 14px;
  }
  .brand-square { width: 22px; height: 22px; background: var(--navy); }
  .brand-name {
    font-family: "Cormorant Garamond", serif; font-weight: 700;
    font-size: 27px; letter-spacing: 2px; text-transform: uppercase;
    color: var(--navy); text-align: center; line-height: 1.1;
  }
  .divider {
    position: absolute; left: 276px; top: 92px; width: 1.5px; height: 184px;
    background: var(--navy);
  }
  .details {
    position: absolute; left: 304px; top: 92px;
    font-family: "Nunito Sans", sans-serif; font-size: 15px; line-height: 1.3;
  }
  .person-name {
    font-family: "Cormorant Garamond", serif; font-weight: 700;
    font-size: 22px; letter-spacing: .5px; text-transform: uppercase; line-height: 1.05;
  }
  .person-role { font-size: 15px; font-weight: 600; margin-bottom: 8px; }
  .address { margin-bottom: 6px; }
  .contact-list { list-style: none; }
  .contact-list li { display: flex; align-items: center; gap: 10px; }
  .contact-icon { width: 12px; height: 12px; fill: none; stroke: var(--navy); stroke-width: 1.6; }

  /* Back */
  .card--back {
    background: radial-gradient(ellipse at 40% 30%, var(--navy) 30%, var(--navy-deep) 100%);
    color: var(--silver);
    display: flex; flex-direction: column; align-items: center; justify-content: center;
  }
  .back-square { width: 30px; height: 30px; background: var(--silver); margin-bottom: 20px; }
  .back-name {
    font-family: "Cormorant Garamond", serif; font-weight: 600;
    font-size: 42px; letter-spacing: 3px; text-transform: uppercase;
  }
  .back-web {
    margin-top: 26px;
    font-family: "Nunito Sans", sans-serif; font-size: 15px; letter-spacing: 3px;
  }
</style>
</head>
<body>
<main class="sheet">

  <section class="card card--front" aria-label="Business card front">
    <div class="front-brand">
      <div class="brand-square"></div>
      <div class="brand-name">Quayview<br>Legal</div>
    </div>
    <div class="divider"></div>
    <div class="details">
      <p class="person-name">Paul Whitcombe</p>
      <p class="person-role">Managing Partner</p>
      <p class="address">Level 9, 7 Ferris Lane<br>Sydney NSW 2000</p>
      <ul class="contact-list">
        <li>
          <svg class="contact-icon" viewBox="0 0 12 12"><path d="M3 1 L5 3.5 L3.8 5 Q5 7.5 7 8.2 L8.5 7 L11 9 L9.5 11 Q4 10.5 1 3 Z"/></svg>
          02 9364 2710
        </li>
        <li>
          <svg class="contact-icon" viewBox="0 0 12 12"><rect x="3" y="1" width="6" height="10" rx="1"/><line x1="5.5" y1="9" x2="6.5" y2="9"/></svg>
          02 8472 3159
        </li>
        <li>
          <svg class="contact-icon" viewBox="0 0 12 12"><rect x="1" y="2.5" width="10" height="7"/><path d="M1 2.5 L6 6.5 L11 2.5"/></svg>
          paul@qvlegal.com.au
        </li>
        <li>
          <svg class="contact-icon" viewBox="0 0 12 12"><circle cx="6" cy="6" r="5"/><ellipse cx="6" cy="6" rx="2.2" ry="5"/><line x1="1" y1="6" x2="11" y2="6"/></svg>
          www.qvlegal.com.au
        </li>
      </ul>
    </div>
  </section>

  <section class="card card--back" aria-label="Business card back">
    <div class="back-square"></div>
    <p class="back-name">Quayview Legal</p>
    <p class="back-web">www.qvlegal.com.au</p>
  </section>

</main>
</body>
</html>
```